Brightfen Business Card Redesign & Logo Update

We need to update our business cards to something more modern and fresh. Brightfen can provide the current color schemes and old design examples, but welcome creativity in helping us with this redesign. PLEASE NOTE that we no longer utilize the "tree" and/or "leaf" imagery in our branding. If able would apprecaite an update on the quality of our "words only" logo in Ai. / PNG formats too.

Target Market(s)

Investors, landowners, corporate partners, contractors

Industry/Entity Type

Environmental Restoration & Conservation

Contact Information for Business Card

Logo, persons name, title, mailing address, phone and email, website url

Font styles to use
Other font styles liked:
• Merriweather

Requirements
Nice to have
• Logo, persons name, title, mailing address, phone and email, website url, but open to ideams
Should not have
• No all back backgrounds

```html
<!DOCTYPE html>
<html lang="en">
<head>
<meta charset="utf-8">
<title>Brightfen Business Card</title>
<link href="https://fonts.googleapis.com/css2?family=Oswald:wght@500;600&family=Montserrat:wght@500;700&display=swap" rel="stylesheet">
<style>
  :root {
    --orange: #ec7d25;
    --green: #1b8240;
    --white: #ffffff;
    --ink: #1e1e1e;
    --page: #d6d6d6;
  }
  html, body {
    margin: 0;
    width: 1200px;
    height: 960px;
    overflow: hidden;
    background: var(--page);
  }
  .card {
    position: absolute;
    left: 250px;
    width: 700px;
    height: 400px;
    overflow: hidden;
    box-shadow: 0 10px 28px rgba(0,0,0,0.25);
  }
  .card--front { top: 45px; background: var(--orange); }
  .card--back { top: 500px; background: var(--white); }

  .wordmark {
    position: absolute;
    font-family: "Oswald", sans-serif;
    font-weight: 600;
    text-transform: uppercase;
    line-height: 1;
  }
  .wordmark__name { display: block; letter-spacing: 2px; }
  .wordmark__tagline { display: block; letter-spacing: 1px; }

  .card--front .wordmark { left: 0; right: 0; top: 118px; text-align: center; color: var(--white); }
  .card--front .wordmark__name { font-size: 116px; }
  .card--front .wordmark__tagline { font-size: 26px; margin-top: 10px; }

  .card__bands { position: absolute; inset: 0; }

  .card--back .wordmark { right: 36px; top: 82px; text-align: right; }
  .card--back .wordmark__name { font-size: 62px; color: var(--orange); }
  .card--back .wordmark__tagline { font-size: 15px; color: var(--ink); margin-top: 5px; }

  .person {
    position: absolute;
    left: 40px;
    top: 108px;
    font-family: "Montserrat", sans-serif;
  }
  .person__name { margin: 0; font-size: 21px; font-weight: 700; letter-spacing: 0.5px; }
  .person__first { color: var(--green); }
  .person__last { color: var(--orange); }
  .person__title { margin: 4px 0 0; font-size: 15px; font-weight: 500; color: var(--ink); }

  .address {
    position: absolute;
    right: 40px;
    top: 196px;
    margin: 0;
    text-align: right;
    font-family: "Montserrat", sans-serif;
    font-style: normal;
    font-size: 15px;
    font-weight: 500;
    line-height: 1.45;
    color: var(--ink);
  }

  .contacts {
    position: absolute;
    left: 40px;
    top: 250px;
    margin: 0;
    padding: 0;
    list-style: none;
    font-family: "Montserrat", sans-serif;
    font-size: 16px;
    font-weight: 500;
    color: var(--ink);
  }
  .contacts__item { display: flex; align-items: center; gap: 12px; height: 30px; }
  .contacts__icon { width: 22px; height: 22px; flex: none; }
</style>
</head>
<body>

<section class="card card--front">
  <div class="wordmark">
    <span class="wordmark__name">Brightfen</span>
    <span class="wordmark__tagline">Environmental Credit Company</span>
  </div>
</section>

<section class="card card--back">
  <svg class="card__bands" viewBox="0 0 700 400" width="700" height="400" aria-hidden="true">
    <!-- top band -->
    <polygon points="0,0 700,0 700,14 310,14 296,68 0,68" fill="var(--orange)"/>
    <polygon points="306,24 700,24 700,32 302,32" fill="var(--green)"/>
    <rect x="300" y="41" width="0" height="0"/>
    <polygon points="296,52 300,44 440,44 440,52" fill="var(--green)"/>
    <rect x="446" y="44" width="70" height="8" fill="var(--orange)"/>
    <rect x="522" y="44" width="178" height="8" fill="var(--green)"/>
    <!-- bottom band -->
    <polygon points="0,400 700,400 700,318 410,318 396,386 0,386" fill="var(--orange)"/>
    <polygon points="0,368 160,368 160,376 0,376" fill="var(--green)"/>
    <rect x="166" y="368" width="70" height="8" fill="var(--orange)"/>
    <polygon points="242,368 402,368 400,376 242,376" fill="var(--green)"/>
    <polygon points="0,348 404,348 402,356 0,356" fill="var(--green)"/>
  </svg>

  <div class="wordmark">
    <span class="wordmark__name">Brightfen</span>
    <span class="wordmark__tagline">Environmental Credit Company</span>
  </div>

  <div class="person">
    <h1 class="person__name"><span class="person__first">DANA</span> <span class="person__last">HOLLOWAY</span></h1>
    <p class="person__title">Managing Director</p>
  </div>

  <address class="address">42 Alder Lane 7<br>Fernhill, OR 97301</address>

  <ul class="contacts">
    <li class="contacts__item">
      <svg class="contacts__icon" viewBox="0 0 22 22" aria-hidden="true">
        <circle cx="11" cy="11" r="11" fill="var(--orange)"/>
        <path d="M7.5 6h2l1 3-1.3 1a6 6 0 0 0 3 3l1-1.3 3 1v2a1.5 1.5 0 0 1-1.5 1.5A9 9 0 0 1 6 7.5 1.5 1.5 0 0 1 7.5 6z" fill="var(--white)"/>
      </svg>
      <span>555-204-3170</span>
    </li>
    <li class="contacts__item">
      <svg class="contacts__icon" viewBox="0 0 22 22" aria-hidden="true">
        <circle cx="11" cy="11" r="11" fill="var(--orange)"/>
        <rect x="5.5" y="7" width="11" height="8" fill="none" stroke="var(--white)" stroke-width="1.4"/>
        <path d="M5.5 7l5.5 4.5L16.5 7" fill="none" stroke="var(--white)" stroke-width="1.4"/>
      </svg>
      <span>info@brightfen.com</span>
    </li>
    <li class="contacts__item">
      <svg class="contacts__icon" viewBox="0 0 22 22" aria-hidden="true">
        <circle cx="11" cy="11" r="11" fill="var(--orange)"/>
        <circle cx="11" cy="11" r="5.5" fill="none" stroke="var(--white)" stroke-width="1.3"/>
        <ellipse cx="11" cy="11" rx="2.4" ry="5.5" fill="none" stroke="var(--white)" stroke-width="1.1"/>
        <path d="M5.5 11h11" stroke="var(--white)" stroke-width="1.1"/>
      </svg>
      <span>www.brightfen.com</span>
    </li>
  </ul>
</section>

</body>
</html>
```